Velmora Freightway Solutions Business cards

Would like a very unique design catchy but professional for business cards. Please use log provided.Marlon WellsCeo and Founder TransCon Logistix Solutions1-888-913-3225mwells@tlsolutionsus.comwww.tlsolutionsus.com

```html
<!DOCTYPE html>
<html lang="en">
<head>
<meta charset="utf-8">
<title>Velmora Freightway Solutions Business Cards</title>
<link href="https://fonts.googleapis.com/css2?family=Open+Sans:wght@400;600;700&display=swap" rel="stylesheet">
<style>
  :root {
    --stage: #1d1d1f;
    --brand-red: #ec1c24;
    --brand-blue: #1170bb;
    --paper: #ffffff;
    --ink-white: #ffffff;
  }
  * { box-sizing: border-box; margin: 0; padding: 0; }
  html, body {
    width: 1200px; height: 960px; overflow: hidden;
    background: var(--stage);
    font-family: "Open Sans", Arial, sans-serif;
  }
  .stage { position: relative; width: 1200px; height: 960px; }

  .card {
    position: absolute;
    width: 560px; height: 320px;
    overflow: hidden;
  }

  /* Front: red face */
  .card--front {
    left: 540px; top: 110px;
    background: var(--brand-red);
    display: flex; flex-direction: column;
    align-items: center; justify-content: center;
    gap: 18px;
  }
  .front-brand {
    display: flex; align-items: center; gap: 16px;
    color: var(--ink-white);
    font-weight: 700; font-size: 34px; line-height: 1.1;
    letter-spacing: 0.5px;
  }
  .front-brand__mark {
    width: 22px; height: 22px; background: var(--ink-white);
  }
  .front-url {
    color: var(--ink-white);
    font-weight: 600; font-size: 15px; letter-spacing: 2px;
  }

  /* Back: info face */
  .card--back {
    left: 100px; top: 530px;
    background: var(--paper);
  }
  .back-brand {
    position: absolute; left: 128px; top: 34px;
    color: var(--brand-blue);
    font-weight: 700; font-size: 25px; line-height: 1.15;
    letter-spacing: 0.3px;
  }
  .back-person {
    position: absolute; left: 128px; top: 112px;
    font-size: 16px; font-weight: 600; text-transform: uppercase;
    color: var(--brand-blue);
  }
  .back-person__title { color: var(--brand-red); font-weight: 400; }

  .panel-blue {
    position: absolute; left: 0; top: 146px;
    width: 432px; height: 174px;
    background: var(--brand-blue);
    border-top-right-radius: 26px;
  }
  .panel-red {
    position: absolute; left: 456px; top: 216px;
    width: 104px; height: 104px;
    background: var(--brand-red);
    border-top-left-radius: 18px;
  }

  .contact-list {
    position: absolute; left: 28px; top: 168px;
    list-style: none;
    color: var(--ink-white);
    font-size: 14.5px; line-height: 26px;
  }
  .contact-list li { display: flex; align-items: center; gap: 9px; }
  .contact-list svg { width: 13px; height: 13px; flex: none; }
  .contact-list .no-icon { padding-left: 0; }
</style>
</head>
<body>
<main class="stage">

  <section class="card card--front" aria-label="Business card front">
    <div class="front-brand">
      <span class="front-brand__mark"></span>
      <span>Velmora Freightway<br>Solutions</span>
    </div>
    <p class="front-url">www.vfwayroutes.com</p>
  </section>

  <section class="card card--back" aria-label="Business card back">
    <div class="back-brand">Velmora Freightway<br>Solutions</div>
    <p class="back-person">Dorian Pike, <span class="back-person__title">CEO and Founder</span></p>

    <div class="panel-blue"></div>
    <div class="panel-red"></div>

    <ul class="contact-list">
      <li>
        <svg viewBox="0 0 16 16" fill="#fff"><path d="M3.6 1.2l2.2 2.6-1.3 1.6c.9 2 2.4 3.6 4.5 4.6l1.6-1.3 2.6 2.2-1.5 2.6C6.3 13 2.9 9.6 1 4.2z"/></svg>
        1-888-470-6158
      </li>
      <li>
        <svg viewBox="0 0 16 16" fill="none" stroke="#fff" stroke-width="1.6"><rect x="1.5" y="3.5" width="13" height="9" rx="1"/><path d="M1.5 4l6.5 5 6.5-5"/></svg>
        dpike@vfwayroutes.com
      </li>
      <li>
        <svg viewBox="0 0 16 16" fill="none" stroke="#fff" stroke-width="1.4"><circle cx="8" cy="8" r="6.5"/><ellipse cx="8" cy="8" rx="2.8" ry="6.5"/><path d="M1.5 8h13"/></svg>
        www.vfwayroutes.com
      </li>
      <li class="no-icon">4417 Larkspur Bend Rd, Atlanta, GA 30342</li>
    </ul>
  </section>

</main>
</body>
</html>
```